Stationary design for boutique production house

We need a stationary design for our production house, 'Lorno Productions' based in Singapore. We produce microfilms as well as podcasts, talkshows and events. Our logo is a stylized icon of our director, who is also the executive producer and host of our programs, Lorno. Our main company colors are Red, Black and white. We would like a clean, minimalist design incorporating our existing company logo that conveys a sense of urbanism and elegance.

Logo and font files are attached. f

Target Market(s)

We focus on lifestyle media rather than entertainment.

Industry/Entity Type

Boutique

Font styles to use
Serif
Sans Serif

Colors
ec1f27
ffffff
000000

Requirements
Must have
• Our company logo and at least one of our company colors.
Nice to have
• Our address and contact information.
Should not have
• Changes made to the company logo (using only certain parts of it is fine though)

```html
<!DOCTYPE html>
<html lang="en">
<head>
<meta charset="utf-8">
<title>Lorno Productions — Business Card</title>
<link rel="stylesheet" href="https://fonts.googleapis.com/css2?family=Jost:wght@400;500&display=swap">
<style>
  :root {
    --brand-red: #ec1f27;
    --brand-black: #000000;
    --ink: #2b2b2b;
    --paper: #ffffff;
    --stage: #3a3a3a;
    --divider: #cfcfcf;
  }
  * { box-sizing: border-box; margin: 0; padding: 0; }
  html, body { width: 1200px; height: 768px; overflow: hidden; }
  body {
    background: var(--stage);
    font-family: "Jost", "Futura", sans-serif;
    display: flex;
    align-items: center;
    justify-content: center;
    gap: 40px;
  }
  .card {
    position: relative;
    width: 540px;
    height: 309px;
    border-radius: 16px;
    overflow: hidden;
  }
  .card__frame {
    position: absolute;
    inset: 12px;
    border-radius: 10px;
  }

  /* Back */
  .card--back { background: var(--brand-red); }
  .card--back .card__frame { border: 1.5px solid var(--paper); }
  .back__mark {
    position: absolute;
    inset: 0;
    display: flex;
    flex-direction: column;
    align-items: center;
    justify-content: center;
    gap: 12px;
  }
  .back__dot { width: 18px; height: 18px; border-radius: 50%; background: var(--paper); }
  .back__name {
    color: var(--paper);
    font-weight: 500;
    font-size: 30px;
    letter-spacing: 3px;
    text-transform: uppercase;
  }
  .back__web {
    position: absolute;
    bottom: 26px;
    width: 100%;
    text-align: center;
    color: var(--paper);
    font-size: 11px;
    letter-spacing: 3px;
  }

  /* Front */
  .card--front { background: var(--paper); }
  .card--front .card__frame { border: 1.5px solid var(--brand-red); }
  .front__brand {
    position: absolute;
    left: 24px; top: 0; bottom: 0;
    width: 200px;
    display: flex;
    flex-direction: column;
    align-items: center;
    justify-content: center;
    gap: 12px;
  }
  .brand__dot { width: 14px; height: 14px; border-radius: 50%; background: var(--brand-red); }
  .brand__name {
    color: var(--brand-black);
    font-weight: 500;
    font-size: 21px;
    letter-spacing: 1.5px;
    text-transform: uppercase;
    text-align: center;
    line-height: 1.15;
  }
  .front__divider {
    position: absolute;
    left: 236px; top: 52px; bottom: 52px;
    width: 1px;
    background: var(--divider);
  }
  .front__details {
    position: absolute;
    left: 262px; top: 58px;
    color: var(--ink);
  }
  .person__name { color: var(--brand-red); font-size: 21px; font-weight: 400; letter-spacing: 1px; line-height: 1; }
  .person__title { font-size: 15px; letter-spacing: 0.5px; margin-top: 3px; }
  .address { font-style: normal; font-size: 13px; line-height: 1.3; margin-top: 12px; letter-spacing: 0.5px; }
  .contacts { list-style: none; margin-top: 8px; font-size: 13px; letter-spacing: 0.6px; }
  .contacts li { display: flex; align-items: center; gap: 8px; height: 19px; }
  .contacts svg { width: 12px; height: 12px; fill: var(--brand-red); flex: none; }
  .contacts .web { padding-left: 20px; }
</style>
</head>
<body>
  <section class="card card--back" aria-label="Card back">
    <div class="card__frame"></div>
    <div class="back__mark">
      <span class="back__dot"></span>
      <span class="back__name">Lorno Productions</span>
    </div>
    <p class="back__web">www.lornostudio.sg</p>
  </section>

  <section class="card card--front" aria-label="Card front">
    <div class="card__frame"></div>
    <div class="front__brand">
      <span class="brand__dot"></span>
      <span class="brand__name">Lorno<br>Productions</span>
    </div>
    <div class="front__divider"></div>
    <div class="front__details">
      <h1 class="person__name">MARA QUINLAN</h1>
      <p class="person__title">CEO/FOUNDER</p>
      <address class="address">214 Keppel Row<br>Tanjong Pagar, Singapore 089112</address>
      <ul class="contacts">
        <li><svg viewBox="0 0 12 12"><path d="M2.5 0.5l2 2.5-1 1.3c.8 1.6 1.9 2.7 3.4 3.4l1.3-1 2.3 2-1 2.3C5.2 10.6 1.4 6.8.6 2.6z"/></svg>612 305 4471</li>
        <li><svg viewBox="0 0 12 12"><path d="M3 0h6a1 1 0 0 1 1 1v10a1 1 0 0 1-1 1H3a1 1 0 0 1-1-1V1a1 1 0 0 1 1-1zm.5 1.5v7.5h5V1.5zM6 9.8a.7.7 0 1 0 0 1.4.7.7 0 0 0 0-1.4z"/></svg>907 218 6630</li>
        <li><svg viewBox="0 0 12 12"><path d="M3 0h6v3H3zM1 4h10a1 1 0 0 1 1 1v4h-2v3H2V9H0V5a1 1 0 0 1 1-1zm2 5v2h6V9z"/></svg>612 305 4479</li>
        <li><svg viewBox="0 0 12 12"><path d="M0 2h12v1.2L6 7 0 3.2zM0 4.6l6 3.8 6-3.8V10H0z"/></svg>mara@lornostudio.sg</li>
        <li><svg viewBox="0 0 12 12"><path d="M6 0a6 6 0 1 0 0 12A6 6 0 0 0 6 0zm0 1.2c.7.8 1.2 2 1.4 3.3H4.6C4.8 3.2 5.3 2 6 1.2zM1.3 5.5h2.3v1H1.3zm7.1 0h2.3v1H8.4zM4.6 7.5h2.8c-.2 1.3-.7 2.5-1.4 3.3-.7-.8-1.2-2-1.4-3.3z"/></svg>www.lornostudio.sg</li>
      </ul>
    </div>
  </section>
</body>
</html>
```